RM Installations Web Site Design

Need a basic site to show clients a little about what we do. We are a custom audio video company in the high-end residential market. Need a few basic but professional pages to show past projects and products we sell. No e-commerce. Should include my new logo from MarkBazaar.

Industry/Entity Type

Residential

Number of Pages Required

2 page

Font styles to use
Serif
Sans Serif

Colors
f78f20

Requirements
Must have
• Company Logo, Send feedback page
Nice to have
• I have no ideas about design, but I do know what I like and dislike when I see it.

```html
<!DOCTYPE html>
<html lang="en">
<head>
<meta charset="utf-8">
<title>RM Installations – Custom Audio Video</title>
<link href="https://fonts.googleapis.com/css2?family=Lato:wght@400;700&family=Oswald:wght@400&display=swap" rel="stylesheet">
<style>
:root{
  --orange:#f78f20;
  --orange-dark:#d9761a;
  --ink:#2e2e2e;
  --text:#4a4a4a;
  --topbar:#3b3b3b;
  --grey-bg:#f0f0f0;
  --white:#ffffff;
}
*{margin:0;padding:0;box-sizing:border-box}
html,body{width:1200px;height:2163px;overflow:hidden;background:var(--white);font-family:'Lato',sans-serif;color:var(--text)}
.page{position:relative;width:1200px;height:2163px}
section,header,footer,.topbar{position:absolute;left:0;width:1200px}
.topbar{top:0;height:26px;background:var(--topbar);color:#eee;font-size:12px}
.topbar .contact{position:absolute;left:170px;top:6px;display:flex;gap:26px}
.topbar .contact span{display:flex;align-items:center;gap:6px}
.topbar .feedback{position:absolute;left:930px;top:0;height:28px;width:96px;background:var(--orange);color:#fff;font-size:12px;text-align:center;line-height:28px;text-transform:uppercase}
.site-header{top:26px;height:76px;background:var(--white)}
.brand{position:absolute;left:170px;top:24px;display:flex;align-items:center;gap:10px;font-size:22px;font-weight:700;color:var(--ink)}
.brand i{width:22px;height:22px;background:var(--orange);display:block}
.nav{position:absolute;left:524px;top:0;display:flex;height:76px;font-size:12px;text-transform:uppercase;color:#555}
.nav a{display:block;padding:0 10px;line-height:84px;color:inherit;text-decoration:none}
.nav a.active{background:var(--orange);color:#fff;width:68px;text-align:center;padding:0}
.hero{top:102px;height:446px;overflow:hidden}
.hero-photo{position:absolute;inset:0;background:linear-gradient(100deg,#cfcad2 0%,#e9e5e6 35%,#8b8a8e 55%,#e6dfe0 75%,#f3eeee 100%)}
.hero-title{position:absolute;left:0;right:0;top:360px;text-align:center;font-family:'Oswald',sans-serif;font-size:52px;font-weight:400;color:#fff;text-shadow:0 2px 6px rgba(0,0,0,.45)}
.hero-arrow{position:absolute;top:234px;width:56px;height:80px;background:rgba(255,255,255,.85)}
.hero-arrow.prev{left:0;border-radius:0 40px 40px 0}
.hero-arrow.next{right:0;border-radius:40px 0 0 40px}
.hero-arrow svg{position:absolute;top:30px}
.hero-arrow.prev svg{left:16px}.hero-arrow.next svg{right:16px}
.section-mark{position:absolute;left:588px;width:24px;height:24px;background:var(--orange)}
.section-title{position:absolute;left:0;right:0;text-align:center;font-size:26px;font-weight:700;color:var(--ink)}
.section-title em{font-style:normal;color:var(--orange)}
.rule{position:absolute;left:446px;width:308px;height:1px;background:#ddd}
.btn{position:absolute;left:539px;width:121px;height:33px;background:var(--orange);color:#fff;font-size:13px;font-weight:700;text-transform:uppercase;text-align:center;line-height:31px;border-bottom:3px solid var(--orange-dark)}
.notch{position:absolute;left:588px;top:0;width:0;height:0;border-left:12px solid transparent;border-right:12px solid transparent}
.about{top:548px;height:320px}
.about p{position:absolute;left:185px;width:830px;top:152px;text-align:center;font-size:13px;line-height:22px}
.services{top:868px;height:372px;background:var(--orange)}
.services .notch{border-top:12px solid var(--white)}
.services .section-mark{top:56px;background:var(--orange-dark)}
.services .section-title{top:104px;color:#fff}
.services .rule{top:152px;background:rgba(255,255,255,.35)}
.service{position:absolute;top:177px;width:150px;margin-left:-75px;text-align:center}
.service .disc{width:104px;height:104px;border-radius:50%;background:#fff;margin:0 auto;display:flex;align-items:center;justify-content:center;box-shadow:0 8px 6px -6px rgba(0,0,0,.25)}
.service.active .disc{background:var(--orange);border:4px solid #fff}
.service p{margin-top:28px;font-size:13px;font-weight:700;color:#fff;line-height:17px}
.side-arrow{position:absolute}
.products{top:1240px;height:459px;background:var(--grey-bg)}
.products .notch{border-top:12px solid var(--orange)}
.products .section-mark{top:60px}
.products .section-title{top:115px}
.products .rule{top:159px}
.card{position:absolute;width:198px;height:170px;overflow:hidden;background:#fff}
.card .photo{position:absolute;inset:0}
.card .label{position:absolute;left:0;right:0;bottom:0;height:35px;background:var(--orange);color:#fff;font-size:14px;text-align:center;line-height:35px}
.projects{top:1699px;height:395px}
.projects .notch{border-top:12px solid var(--grey-bg)}
.projects .section-mark{top:58px}
.projects .section-title{top:110px}
.projects .rule{top:154px}
.projects .card{top:186px;overflow:visible}
.badge{position:absolute;right:-10px;top:-12px;width:32px;height:32px;border-radius:50%;background:var(--orange);border:3px solid #fff;color:#fff;font-size:15px;text-align:center;line-height:26px}
.overlay-text{position:absolute;inset:0;background:rgba(30,30,30,.55);color:#fff;font-size:12px;font-weight:700;line-height:14px;text-align:center;padding:46px 14px 0}
.site-footer{top:2094px;height:69px;background:var(--orange);color:#fff}
.footer-links{position:absolute;left:170px;top:16px;font-size:12px;text-transform:uppercase;white-space:nowrap}
.footer-links span{margin:0 5px}
.copyright{position:absolute;left:170px;top:41px;font-size:12px}
.footer-mark{position:absolute;left:698px;top:22px;width:26px;height:26px;background:var(--orange-dark)}
.social{position:absolute;left:782px;top:22px;display:flex;align-items:center;gap:8px;font-size:17px}
.social i{display:block;width:26px;height:26px;border:2px solid #fff;border-radius:50%}
.social b{font-weight:400;margin-right:6px}
</style>
</head>
<body>
<div class="page">

  <div class="topbar">
    <div class="contact">
      <span><svg width="11" height="12" viewBox="0 0 11 12"><path d="M2 0h2l1 3-1.5 1a7 7 0 0 0 3.5 4l1-1.5 3 1v2c0 1-1 2-2 2A9 9 0 0 1 0 2C0 1 1 0 2 0z" fill="#ddd"/></svg>123-456-7890</span>
      <span><svg width="12" height="9" viewBox="0 0 12 9"><rect width="12" height="9" fill="#ddd"/><path d="M0 0l6 5 6-5" stroke="#3b3b3b" fill="none"/></svg>info@rminstallations.com</span>
    </div>
    <div class="feedback">Feed back</div>
  </div>

  <header class="site-header">
    <div class="brand"><i></i>RM Installations</div>
    <nav class="nav">
      <a class="active">Home</a><a>About</a><a>What we do</a><a>Products</a><a>Past projects</a><a>Contact</a>
    </nav>
  </header>

  <section class="hero">
    <div class="hero-photo" role="img" aria-label="Living room with a hand holding a phone showing a home control app"></div>
    <div class="hero-arrow prev"><svg width="14" height="20" viewBox="0 0 14 20"><path d="M12 2L4 10l8 8" stroke="#333" stroke-width="4" fill="none"/></svg></div>
    <div class="hero-arrow next"><svg width="14" height="20" viewBox="0 0 14 20"><path d="M2 2l8 8-8 8" stroke="#333" stroke-width="4" fill="none"/></svg></div>
    <h1 class="hero-title">We Are Custom Audio Video Company</h1>
  </section>

  <section class="about">
    <div class="section-mark" style="top:46px"></div>
    <h2 class="section-title" style="top:96px">About <em>RM</em> Installations</h2>
    <p>Lorem ipsum dolor sit amet, consectetuer adipiscing elit, sed diam nonummy nibh euismod tincidunt ut laoreet dolore magna aliquam erat volutpat. Ut wisi enim ad minim veniam, quis nostrud exerci tation ullamcorper suscipit lobortis nisl ut aliquip ex ea commodo consequat. Duis autem vel eum iriure dolor in hendrerit in vulputate velit esse molestie consequat, vel illum dolore eu feugiat nulla facilisis at vero erose.</p>
    <div class="btn" style="top:235px">Read more</div>
  </section>

  <section class="services">
    <div class="notch"></div>
    <div class="section-mark"></div>
    <h2 class="section-title">Our services</h2>
    <div class="rule"></div>
    <svg class="side-arrow" style="left:126px;top:220px" width="14" height="22" viewBox="0 0 14 22"><path d="M12 2L3 11l9 9" stroke="#8a4a10" stroke-width="3" fill="none"/></svg>
    <svg class="side-arrow" style="left:1060px;top:220px" width="14" height="22" viewBox="0 0 14 22"><path d="M2 2l9 9-9 9" stroke="#8a4a10" stroke-width="3" fill="none"/></svg>

    <div class="service active" style="left:223px">
      <div class="disc"><svg width="56" height="48" viewBox="0 0 56 48"><path d="M4 16h10L28 4v40L14 32H4z" fill="#333"/><path d="M34 16a10 10 0 0 1 0 16M40 10a18 18 0 0 1 0 28M46 4a26 26 0 0 1 0 40" stroke="#333" stroke-width="4" fill="none"/></svg></div>
      <p>Distributed<br>Video</p>
    </div>
    <div class="service" style="left:369px">
      <div class="disc"><svg width="60" height="50" viewBox="0 0 60 50"><rect x="14" y="6" width="40" height="18" rx="3" transform="rotate(20 34 15)" fill="none" stroke="#555" stroke-width="4"/><path d="M20 30l-4 10H4M4 34v14" stroke="#555" stroke-width="4" fill="none"/></svg></div>
      <p>Security Camera<br>Systems</p>
    </div>
    <div class="service" style="left:519px">
      <div class="disc"><svg width="62" height="40" viewBox="0 0 62 40"><rect x="2" y="2" width="18" height="36" rx="2" fill="#444"/><rect x="42" y="2" width="18" height="36" rx="2" fill="#444"/><rect x="20" y="16" width="22" height="22" fill="#444"/><circle cx="11" cy="26" r="6" fill="#fff"/><circle cx="51" cy="26" r="6" fill="#fff"/><circle cx="11" cy="10" r="3" fill="#fff"/><circle cx="51" cy="10" r="3" fill="#fff"/></svg></div>
      <p>Residential<br>Cinemas</p>
    </div>
    <div class="service" style="left:661px">
      <div class="disc"><svg width="60" height="60" viewBox="0 0 60 60"><circle cx="30" cy="30" r="11" fill="#444"/><g stroke="#444" stroke-width="4"><path d="M30 4v10M30 46v10M4 30h10M46 30h10M12 12l7 7M41 41l7 7M48 12l-7 7M19 41l-7 7"/></g></svg></div>
      <p>Automated<br>Lighting Control</p>
    </div>
    <div class="service" style="left:805px">
      <div class="disc"><svg width="56" height="54" viewBox="0 0 56 54"><path d="M6 40V28a22 22 0 0 1 44 0v12" stroke="#444" stroke-width="4" fill="none"/><rect x="4" y="32" width="12" height="20" rx="4" fill="#444"/><rect x="40" y="32" width="12" height="20" rx="4" fill="#444"/></svg></div>
      <p>Outdoor Audio<br>and Video</p>
    </div>
    <div class="service" style="left:962px">
      <div class="disc"><svg width="60" height="50" viewBox="0 0 60 50"><rect x="22" y="2" width="16" height="12" fill="#444"/><path d="M30 14v10M8 24h44M8 24v10M30 24v10M52 24v10" stroke="#444" stroke-width="3" fill="none"/><rect x="0" y="34" width="16" height="12" fill="#444"/><rect x="22" y="34" width="16" height="12" fill="#444"/><rect x="44" y="34" width="16" height="12" fill="#444"/></svg></div>
      <p>Residential<br>Computer Networks</p>
    </div>
  </section>

  <section class="products">
    <div class="notch"></div>
    <div class="section-mark"></div>
    <h2 class="section-title">Our <em>Products</em></h2>
    <div class="rule"></div>
    <svg class="side-arrow" style="left:126px;top:244px" width="14" height="22" viewBox="0 0 14 22"><path d="M12 2L3 11l9 9" stroke="#777" stroke-width="3" fill="none"/></svg>
    <svg class="side-arrow" style="left:1060px;top:244px" width="14" height="22" viewBox="0 0 14 22"><path d="M2 2l9 9-9 9" stroke="#777" stroke-width="3" fill="none"/></svg>

    <div class="card" style="left:170px;top:185px"><div class="photo" role="img" aria-label="Security cameras beside a monitor with camera feeds" style="background:linear-gradient(135deg,#e8e8e8,#5a6068 60%,#2a2a2a)"></div><div class="label">Security Camera Systems</div></div>
    <div class="card" style="left:391px;top:185px"><div class="photo" role="img" aria-label="Red media room with television and speakers" style="background:linear-gradient(180deg,#c0201e,#9c1414 60%,#2a0c0c)"></div><div class="label">Media Rooms</div></div>
    <div class="card" style="left:612px;top:185px"><div class="photo" role="img" aria-label="Outdoor television on a patio showing a ball game" style="background:linear-gradient(180deg,#3a3a3a,#6b8c5a 55%,#9cb0a0)"></div><div class="label">Outdoor Audio and Video</div></div>
    <div class="card" style="left:832px;top:185px"><div class="photo" role="img" aria-label="Hand holding a phone with a lighting control app in a living room" style="background:linear-gradient(135deg,#8a7050,#c9ae86 50%,#5a4a36)"></div><div class="label">Automated Lighting Control</div></div>

    <div class="btn" style="top:390px">See all</div>
  </section>

  <section class="projects">
    <div class="notch"></div>
    <div class="section-mark"></div>
    <h2 class="section-title">Past <em>Projects</em></h2>
    <div class="rule"></div>

    <div class="card" style="left:170px"><div class="photo" role="img" aria-label="Installer wiring equipment" style="background:linear-gradient(135deg,#6a5a48,#3a3430)"></div><div class="overlay-text">Lorem ipsum dolor sit amet, consectetuer adipiscing elit, sed diam nonummy nibh euismod tincidunt ut laoreet dolore magna aliquam erat volutpat lorem</div><div class="badge">1</div></div>
    <div class="card" style="left:391px"><div class="photo" role="img" aria-label="Security monitoring screens in an office" style="background:linear-gradient(135deg,#8aa0b4,#3e4a56 60%,#9aa8b0)"></div><div class="badge">2</div></div>
    <div class="card" style="left:612px"><div class="photo" role="img" aria-label="Wall lighting control keypad and remote" style="background:linear-gradient(135deg,#7a6a4a,#a89470 50%,#5a4c34)"></div><div class="badge">3</div></div>
    <div class="card" style="left:832px"><div class="photo" role="img" aria-label="Technician with tools on a ladder" style="background:linear-gradient(135deg,#f4f4f4,#2e3a6a 55%,#c8a050)"></div><div class="badge">4</div></div>
  </section>

  <footer class="site-footer">
    <div class="footer-links">Home<span>|</span>About<span>|</span>What we do<span>|</span>Products<span>|</span>Past projects<span>|</span>Contact</div>
    <div class="copyright">© 2015 RMInstallations.com. All Rights Reserved.</div>
    <div class="footer-mark"></div>
    <div class="social"><b>Follow Us on:</b><i></i><i></i><i></i><i></i></div>
  </footer>

</div>
</body>
</html>
```